Business Card for Industrial Distributor

We need a business card design for an industrial distributor. We sell machine parts for the manufacturing and oil industry. We would like the cards to look clean and modern but with a touch of industry.

Our colors are blue/white.

Please feel free to visit our website www.korvelpartsco.com

Target Market(s)

mexican manufacturers in the automobile/aerospace industry

Industry/Entity Type

Industrial

Colors
ffffff
0555a3

```html
<!DOCTYPE html>
<html lang="en">
<head>
<meta charset="utf-8">
<title>Korvel Business Card</title>
<link rel="stylesheet" href="https://fonts.googleapis.com/css2?family=Source+Sans+3:wght@400;600;700&display=swap">
<style>
  :root {
    --backdrop: #141414;
    --card-white: #f5f7f4;
    --brand-navy: #2e3192;
    --brand-blue: #0555a3;
    --card-blue: #2247a8;
    --card-blue-light: #1d5fc0;
    --text-dark: #231f20;
    --white: #ffffff;
  }
  * { margin: 0; padding: 0; box-sizing: border-box; }
  html, body { width: 1200px; height: 900px; overflow: hidden; }
  body {
    background: var(--backdrop);
    font-family: "Source Sans 3", "Myriad Pro", sans-serif;
    position: relative;
  }
  .card {
    position: absolute;
    top: 170px;
    width: 347px;
    height: 561px;
    overflow: hidden;
  }
  .card--front { left: 259px; background: var(--card-white); }
  .card--back { left: 631px; background: var(--card-blue); }
  .card-art { position: absolute; inset: 0; width: 100%; height: 100%; }

  .brand-name {
    position: absolute;
    left: 0; right: 0;
    top: 252px;
    text-align: center;
    font-weight: 700;
    font-size: 26px;
    letter-spacing: 2px;
    color: var(--brand-navy);
  }
  .contact {
    position: absolute;
    left: 0; right: 0;
    top: 315px;
    text-align: center;
    color: var(--text-dark);
  }
  .contact-name {
    font-weight: 700;
    font-size: 19px;
    color: var(--brand-navy);
    line-height: 24px;
  }
  .contact-role { font-size: 15px; line-height: 18px; margin-bottom: 18px; }
  .contact-line { font-size: 15px; line-height: 20px; }
  .contact-label { font-weight: 700; color: var(--brand-navy); margin-right: 4px; }
  .contact-address { font-size: 15px; line-height: 20px; margin-top: 10px; }
</style>
</head>
<body>

<section class="card card--front">
  <svg class="card-art" viewBox="0 0 347 561" aria-hidden="true">
    <defs>
      <radialGradient id="mark-fill" cx="0.45" cy="0.3" r="0.75">
        <stop offset="0" stop-color="#1a7ac8"/>
        <stop offset="1" stop-color="#2a3a9e"/>
      </radialGradient>
    </defs>
    <path class="band band--top" d="M89 0 H257 V50 Q173 20 89 50 Z" fill="var(--brand-navy)"/>
    <path class="band band--bottom" d="M89 561 H257 V520 Q173 550 89 520 Z" fill="var(--brand-navy)"/>
    <circle class="brand-dot" cx="173" cy="155" r="80" fill="url(#mark-fill)"/>
  </svg>
  <div class="brand-name">KORVEL</div>
  <div class="contact">
    <div class="contact-name">MARISOL ORTEGA</div>
    <div class="contact-role">Sales Director</div>
    <div class="contact-line"><span class="contact-label">P:</span> (052) 481 730 265</div>
    <div class="contact-line"><span class="contact-label">M:</span>(052)819246073</div>
    <div class="contact-line"><span class="contact-label">E:</span> info@korvelparts.com</div>
    <div class="contact-line"><span class="contact-label">W:</span>www.korvelpartsco.com</div>
    <div class="contact-address">4820,Av. Industrial Norte,<br>Monterrey, Mexico,64000</div>
  </div>
</section>

<section class="card card--back">
  <svg class="card-art" viewBox="0 0 347 561">
    <defs>
      <radialGradient id="glow" cx="0.5" cy="0.5" r="0.5">
        <stop offset="0" stop-color="#1a63c6"/>
        <stop offset="0.85" stop-color="#1e55b8"/>
        <stop offset="1" stop-color="#2450b0"/>
      </radialGradient>
    </defs>
    <circle class="back-glow" cx="173" cy="285" r="258" fill="url(#glow)"/>
    <circle class="brand-dot" cx="173" cy="445" r="40" fill="var(--white)"/>
    <text class="brand-wordmark" transform="translate(199 390) rotate(-90)"
          font-family="'Source Sans 3', sans-serif" font-weight="700" font-size="74"
          fill="var(--white)">Korvel</text>
    <text class="back-url" transform="translate(271 370) rotate(-90)"
          font-family="'Source Sans 3', sans-serif" font-size="14"
          fill="var(--white)">www.korvelpartsco.com</text>
  </svg>
</section>

</body>
</html>
```